Animal Eye Clinic needs a Business card

We are a new veterinary ophthalmology practice (Ridgeline Pet Vision Care) and we need a business card designed. We only see animal eyes - we are not a regular veterinary clinic. We already have a logo. We are looking for a professional, good looking business card to hand out to our clients. We are looking for something simple but professional and contemporary. Our logo is likely the only picture/graphic that needs to be on the card.
Updates

Contact Information for Business Card

Delia Vossman, BSc, DVM, MSc, DipACVO
Veterinary Ophthalmologist

Phone: 250.418.3927
Email: ridgelinepetvisioncare@mailbox-example.net
Website: ridgelinepetvisioncare-example.net
Address: 1874 Thornbury Rd
Kelowna, BC, V1X 4M9

Colors

Designer to choose colors to be used in the design.

Requirements
Must have
• Our logo (attached)

```html
<!DOCTYPE html>
<html lang="en">
<head>
<meta charset="utf-8">
<title>Ridgeline Pet Vision Care — Business Card</title>
<link href="https://fonts.googleapis.com/css2?family=Roboto:wght@300;400;500&display=swap" rel="stylesheet">
<style>
  :root {
    --backdrop: #e4e2df;
    --card: #2e2f31;
    --card-edge: #1b9aaa;
    --teal: #1b9aaa;
    --ink-light: #f1f1f1;
    --emboss: #3d3e41;
    --divider: #9a9b9d;
  }
  * { box-sizing: border-box; margin: 0; padding: 0; }
  html, body {
    width: 1200px; height: 716px; overflow: hidden;
    background: var(--backdrop);
    font-family: "Roboto", Arial, sans-serif;
  }
  .sheet {
    width: 1200px; height: 716px;
    display: flex; align-items: center; justify-content: center; gap: 60px;
  }
  .card {
    position: relative;
    width: 520px; height: 297px;
    background: var(--card);
    border: 2px solid var(--card-edge);
    box-shadow: 0 10px 26px rgba(0,0,0,.25);
    overflow: hidden;
  }
  /* Front */
  .card--front { display: flex; align-items: center; justify-content: center; }
  .wordmark {
    display: flex; align-items: center; gap: 14px;
  }
  .wordmark__dot {
    width: 46px; height: 46px; border-radius: 50%; flex: none;
  }
  .wordmark__name {
    font-weight: 500; letter-spacing: .02em; line-height: 1.15;
  }
  .card--front .wordmark__dot { background: var(--emboss); width: 64px; height: 64px; }
  .card--front .wordmark__name { color: var(--emboss); font-size: 30px; }

  /* Back */
  .card--back .wordmark {
    position: absolute; left: 34px; top: 110px;
  }
  .card--back .wordmark__dot { background: var(--teal); width: 40px; height: 40px; }
  .card--back .wordmark__name { color: var(--teal); font-size: 17px; width: 150px; }
  .divider {
    position: absolute; left: 238px; top: 88px;
    width: 1px; height: 138px; background: var(--divider);
  }
  .contact {
    position: absolute; left: 256px; top: 84px; right: 14px;
    color: var(--ink-light); font-weight: 300; font-size: 12.5px; line-height: 1.45;
  }
  .contact__name { color: var(--teal); font-weight: 500; font-size: 14px; }
  .contact__creds { color: var(--teal); font-weight: 400; font-size: 9px; }
  .contact__role { margin-bottom: 6px; }
  .contact__address { margin-bottom: 6px; }
  .contact__line { display: flex; align-items: center; gap: 6px; white-space: nowrap; }
  .contact__line svg { width: 10px; height: 10px; flex: none; fill: var(--teal); }
  .contact__email { font-size: 11px; }
  .contact__web-domain { color: var(--teal); }
</style>
</head>
<body>
<main class="sheet">
  <section class="card card--front" aria-label="Card front">
    <div class="wordmark">
      <span class="wordmark__dot"></span>
      <span class="wordmark__name">Ridgeline Pet<br>Vision Care</span>
    </div>
  </section>

  <section class="card card--back" aria-label="Card back">
    <div class="wordmark">
      <span class="wordmark__dot"></span>
      <span class="wordmark__name">Ridgeline Pet Vision Care</span>
    </div>
    <div class="divider"></div>
    <div class="contact">
      <div><span class="contact__name">Delia Vossman</span><span class="contact__creds">, BSc, DVM, MSc, DipACVO</span></div>
      <div class="contact__role">Veterinary Ophthalmologist</div>
      <div class="contact__address">1874 Thornbury Rd<br>Kelowna, BC, V1X 4M9</div>
      <div class="contact__line">
        <svg viewBox="0 0 24 24" aria-hidden="true"><path d="M6.6 10.8a15.1 15.1 0 0 0 6.6 6.6l2.2-2.2a1 1 0 0 1 1-.25 11.4 11.4 0 0 0 3.6.57 1 1 0 0 1 1 1V20a1 1 0 0 1-1 1A17 17 0 0 1 3 4a1 1 0 0 1 1-1h3.5a1 1 0 0 1 1 1c0 1.25.2 2.45.57 3.57a1 1 0 0 1-.25 1z"/></svg>
        <span>250.418.3927</span>
      </div>
      <div class="contact__line">
        <svg viewBox="0 0 24 24" aria-hidden="true"><path d="M2 5h20v14H2z M2 5l10 8 10-8" /></svg>
        <span class="contact__email">ridgelinepetvisioncare@mailbox-example.net</span>
      </div>
      <div class="contact__line">
        <svg viewBox="0 0 24 24" aria-hidden="true"><circle cx="12" cy="12" r="10"/></svg>
        <span>www.<span class="contact__web-domain">ridgelinepetvisioncare-example</span>.net</span>
      </div>
    </div>
  </section>
</main>
</body>
</html>
```